Physiotherapist for Horse and Rider

I need a web design and a working, functioning website for my profession as physiotherapist. Tabs available for the therapy I offer such a massage, stretching, taping, elektrotherapie en advies. Another tab for introducing myself and one for workshops I want to give. I like a tab for photo's and one for how the clients can contact me.

I like it similar too velarun.be Not too much text to read, a beautifull design with matching colours and nice photo's.

Target Market(s)

horse people

Industry/Entity Type

Massage

Number of Pages Required

1 page

Font styles to use
Serif
Script

Colors
34a6d7
0355a3
0493ce

Requirements
Must have
• I like the blue colours from my logo design.
• Contact with e-mail.
• domain name Trotvale Soin
Nice to have
• some off the photo's I uploaded

```html
<!DOCTYPE html>
<html lang="nl">
<head>
<meta charset="utf-8">
<title>Trotvale Soin – Fysiotherapie voor paard en ruiter</title>
<link href="https://fonts.googleapis.com/css2?family=Open+Sans:wght@400;600;700;800&display=swap" rel="stylesheet">
<style>
:root{
  --blue-dark:#0d4fa3;
  --blue-mid:#0493ce;
  --blue-light:#34a6d7;
  --bar-dark:#0b4a9e;
  --dark:#2b2b2b;
  --dark-2:#242424;
  --text:#444;
  --muted:#bbb;
  --white:#fff;
  --border:#d6d6d6;
}
*{box-sizing:border-box;margin:0;padding:0}
html,body{width:1200px;height:3237px;overflow:hidden}
body{font-family:"Open Sans",Arial,sans-serif;color:var(--text);background:var(--white);position:relative}
.abs{position:absolute}
/* hero */
.hero{left:0;top:0;width:1200px;height:615px;background:linear-gradient(100deg,#5a4a3a 0%,#8b7a64 35%,#a69884 55%,#6e5d49 80%,#3f342a 100%)}
.logo{left:132px;top:0;width:233px;height:177px;background:var(--white);display:flex;flex-direction:column;align-items:center;justify-content:center;gap:6px}
.logo-mark{width:46px;height:46px;border-radius:50%;background:var(--blue-mid)}
.logo-name{font-size:25px;font-weight:600;color:var(--blue-mid);letter-spacing:.5px}
.nav{left:383px;top:14px;display:flex;gap:26px;font-size:11px;text-transform:uppercase;color:#eee;letter-spacing:.3px}
.nav .active{border-bottom:1px solid #eee;padding-bottom:3px;font-weight:600}
.hero-title{left:0;top:290px;width:1200px;text-align:center;color:var(--white);font-weight:700;text-shadow:0 2px 6px rgba(0,0,0,.4)}
.hero-title .l1{font-size:33px;line-height:40px;display:block}
.hero-title .l2{font-size:50px;line-height:60px;display:block}
.btn-hero{left:480px;top:392px;width:240px;height:50px;background:var(--blue-mid);color:var(--white);font-size:14px;font-weight:700;display:flex;align-items:center;justify-content:center;text-transform:uppercase}
.dots{left:558px;top:582px;display:flex;gap:14px}
.dots span{width:9px;height:9px;border-radius:50%;background:var(--white)}
.dots span:first-child{background:none;border:1px solid var(--white)}
/* welcome */
.section-title{width:1200px;left:0;text-align:center;color:var(--blue-dark);font-weight:800;font-size:34px}
.lead{left:130px;width:940px;text-align:center;font-size:12.5px;line-height:22px;color:#333}
.portrait{left:552px;top:853px;width:96px;height:96px;background:linear-gradient(160deg,#8f8a7c,#5c8f6a)}
/* dark band */
.band-photo{left:0;top:1030px;width:600px;height:392px;background:linear-gradient(120deg,#3a332c,#6e6457 50%,#2f6b4c 75%,#2a2520)}
.band-text{left:600px;top:1030px;width:600px;height:392px;background:var(--dark);padding:48px 60px 0 40px;color:#ddd;font-size:11.5px;line-height:19px}
.band-text p{margin-bottom:16px}
.band-text ul{list-style:none;margin:-4px 0 16px}
.band-text li{font-size:14px;line-height:30px}
.band-text li::before{content:"›";margin-right:10px}
/* treatments */
.sub-title{left:0;width:1200px;text-align:center;color:var(--blue-light);font-size:20px;font-weight:400}
.card{top:1652px;width:218px}
.card-img{height:160px}
.card h3{font-size:16px;font-weight:700;color:#222;margin:14px 0 4px;text-transform:uppercase}
.card p{font-size:10.5px;line-height:17px;color:#333}
.card a{color:var(--blue-dark);font-weight:600;text-decoration:none}
.advice{left:132px;top:1940px;width:935px;height:95px;border:2px solid var(--border);background:#f4f4f4;padding:22px 30px;font-size:12px;line-height:22px;color:#333;text-align:center}
.advice .i{display:inline-block;width:12px;height:12px;border-radius:50%;background:#555;margin-right:8px;vertical-align:-1px}
/* photos + workshops */
.photo-l{left:0;top:2115px;width:600px;height:392px;background:linear-gradient(135deg,#e0dcd2,#8a6a4a 45%,#4f9fc0 70%,#d8d6cf)}
.photo-r{left:600px;top:2115px;width:600px;height:392px;background:linear-gradient(135deg,#6b5240,#a2724a 45%,#4aa6cf 70%,#b9a58c)}
.workshop{top:2507px;width:600px;height:96px;color:var(--white);padding:22px 0 0 130px}
.workshop.left{left:0;background:var(--bar-dark)}
.workshop.right{left:600px;background:var(--blue-light);padding-left:40px}
.workshop small{display:block;font-size:12px;font-weight:700;text-transform:uppercase}
.workshop strong{display:block;font-size:20px;font-weight:700;text-transform:uppercase;margin-top:4px}
/* contact */
.contact-row{left:132px;top:2745px;width:935px;display:flex;justify-content:space-between;font-size:14px;color:#222;align-items:center}
.contact-row span{display:flex;align-items:center;gap:6px}
.footer{left:0;top:2797px;width:1200px;height:440px;background:var(--dark)}
.qc{left:0;top:2855px;width:1200px;text-align:center;color:var(--white);font-size:18px}
.field{height:43px;border:1px solid #555;color:#888;font-size:11px;padding:14px 12px}
.submit{left:560px;top:3030px;width:80px;height:40px;background:var(--blue-dark);color:var(--white);font-size:12px;font-weight:700;display:flex;align-items:center;justify-content:center}
.rule{left:0;top:3133px;width:1200px;height:1px;background:#3d3d3d}
.flinks{left:132px;top:3163px;font-size:10.5px;color:#ccc}
.flinks span{margin:0 8px}
.copy{left:132px;top:3192px;font-size:10.5px;color:#aaa}
.social{left:912px;top:3170px;display:flex;gap:8px}
.social span{width:24px;height:24px;border-radius:50%;background:var(--blue-light)}
</style>
</head>
<body>

<header class="abs hero" role="img" aria-label="Foto: therapeute behandelt een bruin paard in de stal"></header>
<div class="abs logo"><div class="logo-mark"></div><div class="logo-name">Trotvale Soin</div></div>
<nav class="abs nav">
  <span class="active">Home</span><span>About us</span><span>Massage</span><span>Stretching</span><span>Taping</span><span>Elektrotherapie en advies</span><span>Photos</span><span>Contact us</span>
</nav>
<h1 class="abs hero-title"><span class="l1">FYSIOTHERAPEUT DIE DOET VOOR</span><span class="l2">PAARD EN RUITER</span></h1>
<div class="abs btn-hero">Neem contact met mij op</div>
<div class="abs dots"><span></span><span></span><span></span><span></span></div>

<h2 class="abs section-title" style="top:688px">WELKOM BIJ TROTVALE SOIN</h2>
<p class="abs lead" style="top:745px">Marie Dewaele, 32 jaar, Trotvale Soin. Marie studeerde af van de Hogeschool Noordkust als humaan kinesitherapeut in 2007. Zij begon onmiddellijk aan de opleiding Dierfysiotherapie in de Faculteit Diergeneeskunde te Lindewijk en studeerde af als Fysiotherapeut voor paarden in 2010. Ze combineert beide als Kinesitherapeut voor Paard en Ruiter. Van jaartal tot jaartal schoolde ze zich bij in de Humane Manuele Therapie. In jaartal leerde ze natuurlijk hoefbekappen. Sinds 2016 heeft ze zich ook verdiept in de Manuele Tapingmethode en Paardentaping.</p>
<div class="abs portrait" role="img" aria-label="Portretfoto van de therapeute"></div>

<div class="abs band-photo" role="img" aria-label="Foto: therapeute masseert de hals van een donker paard"></div>
<div class="abs band-text">
  <p>Als mens compenseren we ook vaak kleine ongemakken, waardoor er een onevenwicht ontstaat tussen bepaalde spieren. Dit heeft een effect op ons paard.</p>
  <p>Voeding is ook zeer belangrijk. Bepaalde voedingsstoffen worden makkelijker opgenomen dan andere. Bij belastende voeding kunnen maagklachten en darmproblemen ontstaan. Dit geeft het paard ongemak tijdens het rijden.</p>
  <ul><li>Maagzuur, lege maag tijdens training</li><li>Tandverzorging, kaakgewricht</li></ul>
  <p>Als kinesitherapeut ga ik op zoek naar de oorzaak van het probleem. In het begin kunnen er sommige symptomen zo drastisch aanwezig zijn dat ze de eigenlijke oorzaak maskeren. Dan moeten deze symptomen eerst behandeld worden, zodat de onderliggende oorzaak ontdekt kan worden.</p>
</div>

<h2 class="abs section-title" style="top:1490px">KINESITHERAPIE VOOR PAARD EN RUITER</h2>
<p class="abs lead" style="top:1536px">Een paard voelt een vlieg zitten op zijn vacht. Het kleinste onevenwicht in spierspanning kan hij dus voelen bij zijn ruiter. Paard en ruiter beïnvloeden elkaar, daarom behandel ik beide om zo tot een ontspannen geheel te komen, waarbij jij en je paard als één functioneren.</p>
<h3 class="abs sub-title" style="top:1606px">BEHANDELINGEN</h3>

<article class="abs card" style="left:132px"><div class="card-img" role="img" aria-label="Foto: massage van een paard" style="background:linear-gradient(135deg,#3b3630,#4f8f62 55%,#2e2a25)"></div><h3>Massage</h3><p>heeft als doel de spieren te ontspannen en te versoepelen, de bloeddoorstroming te stimuleren, voedingsstoffen aan en... <a>More</a></p></article>
<article class="abs card" style="left:371px"><div class="card-img" role="img" aria-label="Foto: stretching van een paardenbeen" style="background:linear-gradient(135deg,#7a6552,#c9c2b4 55%,#6e5a45)"></div><h3>Stretching</h3><p>houdt de spieren en de pezen soepel en op lengte. Na een spierscheur wordt het nieuwe gevormde littekenw... <a>More</a></p></article>
<article class="abs card" style="left:611px"><div class="card-img" role="img" aria-label="Foto: elektrotherapie bij een paard" style="background:linear-gradient(135deg,#2f2a26,#5a4c40 50%,#4f8f62)"></div><h3>Elektrotherapie</h3><p>pijnstillende stroom, genaamd TENS, geeft kleine trillingen in de spiervezels waardoor deze ontspannen. <a>More</a></p></article>
<article class="abs card" style="left:850px"><div class="card-img" role="img" aria-label="Foto: taping bij een paard" style="background:linear-gradient(135deg,#4f8f62,#6a5646 50%,#2e2925)"></div><h3>Taping</h3><p>Door in het verloop van spieren te tapen, kan je de spier helpen ontspannen of net extra activeren. <a>More</a></p></article>

<div class="abs advice"><span class="i"></span>Advies:Tijdens een behandeling let ik ook op de stand van de benen en de staat van de hoeven. Ook het kaakgewricht en de tanden worden gecontroleerd. Bij een vermoeden van drukpunten wordt het zadel nagekeken. Indien nodig zal ik u doorverwijzen. Stel gerust uw vragen. We zoeken samen een oplossing.</div>

<div class="abs photo-l" role="img" aria-label="Foto: therapeute behandelt een bruin paard op een binnenplaats"></div>
<div class="abs photo-r" role="img" aria-label="Foto: therapeute legt haar hand op het hoofd van een paard"></div>
<div class="abs workshop left"><small>Workshops</small><strong>Zelf je paard masseren</strong></div>
<div class="abs workshop right"><small>Workshops</small><strong>Wellnessweekend voor paard en ruiter</strong></div>

<h2 class="abs section-title" style="top:2672px">CONTACT</h2>
<div class="abs contact-row">
  <span><svg width="11" height="14" viewBox="0 0 11 14"><path d="M5.5 0A5.5 5.5 0 0 0 0 5.5C0 9.6 5.5 14 5.5 14S11 9.6 11 5.5A5.5 5.5 0 0 0 5.5 0zm0 7.5a2 2 0 1 1 0-4 2 2 0 0 1 0 4z" fill="#222"/></svg>24 Building name, Street name, City- Zipcode</span>
  <span><svg width="9" height="14" viewBox="0 0 9 14"><rect x=".5" y=".5" width="8" height="13" rx="1.5" fill="none" stroke="#222"/><rect x="3" y="11" width="3" height="1" fill="#222"/></svg>654 321 6485</span>
  <span><svg width="15" height="13" viewBox="0 0 15 13"><rect x="0" y="4" width="15" height="9" rx="1" fill="#222"/><rect x="3" y="0" width="9" height="5" fill="#222"/><rect x="4" y="7" width="7" height="4" fill="#fff"/></svg>546 321 5548</span>
  <span><svg width="14" height="11" viewBox="0 0 14 11"><rect width="14" height="11" fill="#222"/><path d="M0 0l7 6 7-6" fill="none" stroke="#fff"/></svg>info@trotvalesoin.be</span>
</div>

<footer class="abs footer"></footer>
<h3 class="abs qc">QUICK CONTACT</h3>
<div class="abs field" style="left:132px;top:2910px;width:218px">Name</div>
<div class="abs field" style="left:371px;top:2910px;width:218px">Email</div>
<div class="abs field" style="left:611px;top:2910px;width:218px">Phone</div>
<div class="abs field" style="left:850px;top:2910px;width:217px">Address</div>
<div class="abs field" style="left:132px;top:2968px;width:935px">Message</div>
<div class="abs submit">SUBMIT</div>
<div class="abs rule"></div>
<div class="abs flinks">Home<span>|</span>About us<span>|</span>Massage<span>|</span>Stretching<span>|</span>Taping<span>|</span>Elektrotherapie en advies<span>|</span>Photos<span>|</span>Contact us</div>
<div class="abs copy">Copyright © 2017 Company name. All rights reserved.</div>
<div class="abs social"><span></span><span></span><span></span><span></span><span></span></div>

</body>
</html>
```